Wordpress Theme for Cedarview Clinics

** Please view updated Sitemap2.pdf doc to clarify some confusion ***

This is a multiuser WordPress subscription site for Cedarview Clinics. Please see attachment for sitemap. Please do not include extra content like social media icons, search bars, or images. If you have questions, please ask for clarification.
The site contains the following pages and sub-pages:

1. Home
2. Our Clinic
2a. Our Clinic > Mission
2b. Our Clinic > Services
2c. Our Clinic > Clinic Policies
2d. Our Clinic > Schedules
3. Our Staff
3a. Our Staff > [Staff member page]
4. Resources
4a. Resources > Patient Health (index)
4b. Resources > Patient Health (index) > [post]
4c. Resources > Links
4d. Resources > Forms
5. Alerts
5a. Alerts > [Alert Page]
6. Contact Us

Includes the Following Pages, Subpages, and Content
1. Home
a. About Us
b. Our Staff
c. Bulletins
d. Accepting New Patients (shown as an alert widget)
e. Links
i. Physician Toolbox
ii. Book an Appointment
f. Clinic Policies
i. Show first 3 policies (e.g. Late Arrivals, Missed Appointments, Fees)
ii. Link to Clinic Policies page
g. Primary widget (displayed on all pages)
i. Hours of operation
ii. Contact Info
1. Tel
2. Fax
3. Email
4. Address
5. Get directions (link to Google Maps)
2. Our Clinic
a. Main Page
i. Clinic Name
ii. Overview
iii. Languages Spoken
iv. Secondary Navigation
1. Mission
2. Services
3. Clinic Policies
4. Schedules (see attachment)
b. Our Clinic > Mission
c. Our Clinic > Services
i. For each service include service TITLE and DESCRIPTION
d. Our Clinic > Clinic Policies
i. For each policy include policy TITLE and DESCRIPTION
ii. Include the following policies in mockup
1. Late arrivals
2. Missed appointments
3. Fees for missed appointments
4. Referrals and follow-ups
5. Services not covered by RDA
6. Information for LTF patients
7. Medical Legal Reports
e. Our Clinic > Schedules
3. Our Staff
a. Main Page
i. Display a list of staff members. Include NAME and DESIGNATION
b. Our Staff > [Staff Name]
i. Include NAME, PICTURE, DESIGNATION, and BIO
4. Resources
a. Resources > Patient Health
i. Main Page
1. Posts (ordered by date)
a. Title
b. Summary
2. Side Navigation
a. Post Categories
ii. Patient Health > [post title]
1. Title
2. Post Category
3. Date
4. Author
5. Summary
6. Body
b. Resources > Links
1. Secondary Navigation - Categories
a. Sample Categories:
i. Local Services
ii. RDA and Drug Coverage
iii. Mental Health Resources
2. Category page
a. Include the following links in the 'Local Services' category
i. Hypertension clinics
ii. Home Care services
iii. Vaccine Clinics
c. Resources > Forms
i. Display a table with form TITLE and CATEGORY
ii. Side Navigation
1. Form Categories
a. Use the following sample Categories
i. Referrals
ii. Insurance
iii. Intake
iv. Discharge
v. Waivers
5. Alerts
a. Main page
i. List of all Alert posts
1. Include post TITLE as a link to the post
ii. Side Navigation
1. Alerts Archive
a. shown as Month + Number of posts
iii. Alerts > [Alert page]
1. Include TITLE, DATE, AUTHOR, BODY
6. Contact Us
a. Map
b. Hours of operation
c. Address
d. Phone number
e. Fax number
e. Fax number
f. Map
g. Email

Design notes:
- fixed width
- responsive (need designs for mobile, tablet, and desktop)
- simple, dark font, white background
- use Font Awesome icons where needed
- user adds own logo

Target Market(s)

Cedarview Clinics

Industry/Entity Type

Medical

Number of Pages Required

5+ page

Font styles to use
Serif
Sans Serif

Requirements
Must have
• Please keep designs very simple.
• Examples:
• https://www.quolbin.com/install
• http://www.ventrohax.com/company/about-us
• http://brindlequota.org/
• http://www.trosk.com/
Should not have
• Minimal or no use of shadows and gradients

```html
<!DOCTYPE html>
<html lang="en">
<head>
<meta charset="utf-8">
<title>Cedarview Clinics – Home</title>
<link href="https://fonts.googleapis.com/css2?family=Lato:wght@300;400;700&display=swap" rel="stylesheet">
<style>
:root{
  --blue:#0f8be0;
  --blue-mid:#0a6fc2;
  --blue-dark:#0b63b0;
  --text:#333;
  --muted:#777;
  --line:#dcdcdc;
  --panel:#f1f1f1;
  --footer:#2a2a2a;
  --footer-base:#202020;
  --footer-text:#8a8a8a;
}
*{box-sizing:border-box;margin:0;padding:0}
html,body{width:846px;height:1200px;overflow:hidden}
body{font-family:"Lato",sans-serif;color:var(--text);background:#fff;position:relative}
a{color:inherit;text-decoration:none}
.abs{position:absolute}

/* top bar */
.topbar{left:0;top:0;width:846px;height:21px;background:var(--blue);color:#fff;font-size:6px}
.topbar .left{left:114px;top:7px}
.topbar .right{right:114px;top:7px}
.topbar .sep{display:inline-block;width:1px;height:11px;background:#fff;vertical-align:middle;margin:0 6px;opacity:.8}

/* header */
.brand{left:114px;top:36px;display:flex;align-items:center;gap:9px}
.brand .dot{width:22px;height:22px;border-radius:50%;background:var(--blue)}
.brand .name{font-size:16px;font-weight:400;color:#2b2b2b}
.nav{left:391px;top:21px;display:flex;height:58px;font-size:7px;color:#444}
.nav a{display:flex;align-items:center;padding:0 14px}
.nav a.active{background:var(--blue);color:#fff;width:42px;justify-content:center;padding:0;margin-right:3px}

/* hero */
.hero{left:114px;top:79px;width:618px;height:211px}
.hero .photo{position:absolute;inset:0;background:linear-gradient(90deg,#8a6a4f 0%,#c8a887 28%,#e7dccd 55%,#d8e3ee 75%,#eef1f4 100%)}
.hero h1{position:absolute;left:24px;top:49px;font-weight:300;font-size:20px;line-height:24px;color:#fff}
.hero h1 span{color:var(--blue);display:block}
.hero p{position:absolute;left:24px;top:104px;width:170px;font-size:7px;line-height:9.5px;color:#fff}
.hero .btn{position:absolute;left:24px;top:141px;width:94px;height:20px;background:var(--blue-mid);color:#fff;font-size:7px;font-weight:700;display:flex;align-items:center;justify-content:center}
.hero .dots{position:absolute;left:30px;top:195px;display:flex;gap:3px}
.hero .dots i{width:5px;height:5px;border-radius:50%;background:#fff}
.hero .dots i.on{background:var(--blue)}
.arrow{width:17px;height:20px;background:var(--blue);color:#fff;display:flex;align-items:center;justify-content:center}
.arrow svg{width:6px;height:6px}

/* info bands */
.info{left:114px;top:290px;width:618px;height:106px;display:flex;color:#fff}
.info section{width:206px;padding:11px 16px 0 17px}
.info .c1{background:var(--blue)}
.info .c2{background:var(--blue-dark)}
.info .c3{background:#0c78d0}
.info h3{font-size:10px;font-weight:400;margin-bottom:8px}
.info .lead{font-size:10px}
.info .contact-btn{display:flex;margin:15px 0 0 41px;width:90px;height:22px;background:#fff;color:var(--blue);font-size:11px;align-items:center;justify-content:center}
.info table{border-collapse:collapse;font-size:7px}
.info td{padding:0;height:10px;vertical-align:top}
.info .c2 td:first-child{width:95px}
.info .c3 td:first-child{width:56px;padding-left:3px}

/* about */
.about-photo{left:114px;top:417px;width:143px;height:164px;border:1px solid var(--line);padding:3px}
.about-photo div{width:100%;height:100%;background:linear-gradient(160deg,#f4f4f4,#dfe5ea)}
.about{left:272px;top:423px;width:245px}
.about h2{font-size:11px;font-weight:400;margin-bottom:7px}
.about .sub{font-size:7.5px;margin-bottom:8px}
.about p{font-size:6.5px;line-height:10.5px;color:var(--muted);margin-bottom:11px}
.btn-sm{display:inline-flex;align-items:center;justify-content:center;background:var(--blue-mid);color:#fff;font-size:7px;font-weight:700;height:18px;padding:0 8px}

.policies{left:537px;top:418px;width:195px;height:163px;border:1px solid var(--line)}
.policies h3{height:22px;background:var(--blue);color:#fff;font-size:11px;font-weight:700;display:flex;align-items:center;justify-content:center}
.policies ul{list-style:none;margin:8px 27px 0 22px;font-size:6.5px;color:var(--blue-mid)}
.policies li{height:14.8px;border-bottom:1px solid #e8e8e8;display:flex;align-items:center}
.policies li:last-child{border-bottom:0}
.policies .btn-sm{position:absolute;left:71px;top:137px;height:16px;width:53px;gap:3px}

.rule{left:114px;top:602px;width:618px;height:1px;background:var(--line)}

/* alerts */
.alerts-title{left:114px;top:621px;font-size:12px;font-weight:400}
.alert{top:641px;width:198px;display:flex;gap:16px}
.alert .date{flex:none;width:37px;height:33px;background:var(--blue);color:#fff;font-size:10px;font-weight:700;line-height:11px;padding:3px 0 0 7px}
.alert .date sup{font-size:6px}
.alert h4{font-size:7.5px;font-weight:400;line-height:10.5px;margin-bottom:4px}
.alert h4.link{color:var(--blue)}
.alert p{font-size:5.5px;line-height:9.3px;color:var(--muted)}
.btn-outline{left:394px;top:704px;width:58px;height:18px;background:var(--blue);color:#fff;font-size:7.5px;display:flex;align-items:center;justify-content:center}

/* staff */
.staff-band{left:0;top:746px;width:846px;height:296px;background:var(--panel)}
.staff-title{left:114px;top:765px;font-size:12px}
.staff-sub{left:114px;top:786px;font-size:7.5px;color:var(--muted)}
.card{top:810px;width:143px;height:169px;background:#fff;border:1px solid var(--line)}
.card .pic{height:132px;background:linear-gradient(180deg,#fbfbfb,#e8edf1)}
.card h5{font-size:9px;font-weight:400;margin:7px 0 2px 5px}
.card span{font-size:7.5px;color:var(--blue);margin-left:5px}
.btn-lg{top:995px;height:25px;color:#fff;font-size:8px;display:flex;align-items:center;justify-content:center}

/* footer */
.footer-line{left:0;top:1042px;width:846px;height:3px;background:var(--blue)}
.footer{left:0;top:1045px;width:846px;height:131px;background:var(--footer);color:var(--footer-text)}
.footer .brand{top:22px}
.footer .brand .name{color:#fff}
.footer .about-f{position:absolute;left:114px;top:60px;width:150px;font-size:5.5px;line-height:9.5px;color:#ccc}
.footer .col{position:absolute;top:22px;font-size:6.5px;line-height:12.8px}
.footer .col h6{font-size:9.5px;font-weight:400;color:#9a9a9a;margin-bottom:3px}
.footer .col .current{color:#fff}
.footer table{border-collapse:collapse;font-size:6.5px;line-height:10.5px}
.footer td{padding:0;vertical-align:top}
.footer td:first-child{width:57px;padding-left:2px}
.base{left:0;top:1176px;width:846px;height:24px;background:var(--footer-base);color:#7a7a7a;font-size:6.5px}
.base .copy{left:114px;top:8px}
.base .links{left:326px;top:8px;display:flex;gap:14px}
</style>
</head>
<body>

<header>
  <div class="abs topbar">
    <span class="abs left">To help Here : 250 418 7720<span class="sep"></span>Email : hello@cedarviewclinics.ca</span>
    <span class="abs right"><a href="#">Book an Appointment</a><span class="sep"></span><a href="#">Physician Toolbox</a></span>
  </div>
  <a class="abs brand" href="#"><span class="dot"></span><span class="name">Cedarview Clinics</span></a>
  <nav class="abs nav">
    <a class="active" href="#">Home</a>
    <a href="#">Our Clinic</a>
    <a href="#">Newsletter</a>
    <a href="#">Our Staff</a>
    <a href="#">Resources</a>
    <a href="#">Contact Us</a>
  </nav>
</header>

<section class="abs hero">
  <div class="photo" role="img" aria-label="Group of smiling doctors and nurses in white coats in a hospital corridor"></div>
  <h1>We Care About<span>Every Patients</span></h1>
  <p>Lorem Ipsum is simply dummy text of the printing and typesetting industry. Lorem Ipsum has been the industry's standard dummy</p>
  <a class="btn" href="#">Make an Appointment</a>
  <div class="dots"><i></i><i></i><i class="on"></i><i></i></div>
</section>
<a class="abs arrow" style="left:105px;top:168px" href="#"><svg viewBox="0 0 6 6"><path d="M4 0.5 1.5 3 4 5.5" fill="none" stroke="#fff" stroke-width="1.2"/></svg></a>
<a class="abs arrow" style="left:724px;top:168px" href="#"><svg viewBox="0 0 6 6"><path d="M2 0.5 4.5 3 2 5.5" fill="none" stroke="#fff" stroke-width="1.2"/></svg></a>

<div class="abs info">
  <section class="c1">
    <h3>New Patients</h3>
    <p class="lead">Accepting new Patients here...</p>
    <a class="contact-btn" href="#">Contact Us</a>
  </section>
  <section class="c2">
    <h3>Hours of Opration</h3>
    <table>
      <tr><td>Monday :</td><td>8:00 AM - 6:00 PM</td></tr>
      <tr><td>Tuesday :</td><td>8:00 AM - 6:00 PM</td></tr>
      <tr><td>Wednesday :</td><td>8:00 AM - 6:00 PM</td></tr>
      <tr><td>Thursday :</td><td>8:00 AM - 6:00 PM</td></tr>
      <tr><td>Friday :</td><td>8:00 AM - 6:00 PM</td></tr>
      <tr><td>Saturday :</td><td>9:00 AM - 4:00 PM</td></tr>
      <tr><td>Sunday :</td><td>9:00 AM - 4:00 PM</td></tr>
    </table>
  </section>
  <section class="c3">
    <h3>Contact Info</h3>
    <table>
      <tr><td>Telephone :</td><td>604-318-4402</td></tr>
      <tr><td>Email:</td><td>hello@cedarviewclinics.ca</td></tr>
      <tr><td>Address:</td><td>48 Alder Row Harbourton,<br>Canada, K2M 7QP</td></tr>
    </table>
  </section>
</div>

<div class="abs about-photo"><div role="img" aria-label="Smiling female doctor holding a clipboard and pen"></div></div>
<section class="abs about">
  <h2>About Us</h2>
  <p class="sub">Lorem Ipsum is simply dummy text of the printing</p>
  <p>Lorem Ipsum is simply dummy text of the printing and typesetting industry. Lorem Ipsum has been the industry's standard dummy text ever since the 1500s, when an unknown printer took a galley of type and scrambled it to make a type specimen book. It has survived not only five centuries, but also the leap into electronic typesetting, remaining essentially unchanged.</p>
  <p>Lorem Ipsum is simply dummy text of the printing and typesetting industry. Lorem Ipsum has been the industry's standard dummy text ever since the 1500s, when an unknown.</p>
  <a class="btn-sm" href="#">Read more</a>
</section>

<aside class="abs policies">
  <h3>Clinic Policies</h3>
  <ul>
    <li>Clinic Policies</li>
    <li>Late arrivals</li>
    <li>Missd appoinmets</li>
    <li>Fees for missed Appoinments</li>
    <li>Referrals and follow-ups</li>
    <li>Services not covered by RDA</li>
    <li>Medical Legal Reports</li>
  </ul>
  <a class="btn-sm" href="#">View All <svg width="7" height="5" viewBox="0 0 7 5"><path d="M0 2.5h6M4 0.5l2 2-2 2" fill="none" stroke="#fff" stroke-width="1"/></svg></a>
</aside>

<div class="abs rule"></div>

<h2 class="abs alerts-title">Alerts/Bulletins</h2>
<article class="abs alert" style="left:114px">
  <div class="date">June<br>25<sup>th</sup></div>
  <div><h4 class="link">Lorem Ipsum is simply dummy text of is simply dummy text of</h4>
  <p>Lorem Ipsum is simply dummy text of the printing and typesetting industry. Lorem Ipsum has been the industry's standard dummy text ever since</p></div>
</article>
<article class="abs alert" style="left:325px">
  <div class="date">June<br>26<sup>th</sup></div>
  <div><h4>Lorem Ipsum is simply dummy text of is simply dummy text of</h4>
  <p>Lorem Ipsum is simply dummy text of the printing and typesetting industry. Lorem Ipsum has been the industry's standard dummy text ever since</p></div>
</article>
<article class="abs alert" style="left:537px">
  <div class="date">June<br>27<sup>th</sup></div>
  <div><h4>Lorem Ipsum is simply dummy text of is simply dummy text of</h4>
  <p>Lorem Ipsum is simply dummy text of the printing and typesetting industry. Lorem Ipsum has been the industry's standard dummy text ever since</p></div>
</article>
<a class="abs btn-outline" href="#">View All</a>

<div class="abs staff-band"></div>
<h2 class="abs staff-title">Our Staff</h2>
<p class="abs staff-sub">Lorem Ipsum is simply dummy text of the printingorem Ipsum is simply dummy text of the printing</p>
<a class="abs arrow" style="left:91px;top:883px;width:18px;height:18px" href="#"><svg viewBox="0 0 6 6"><path d="M4 0.5 1.5 3 4 5.5" fill="none" stroke="#fff" stroke-width="1.2"/></svg></a>
<a class="abs arrow" style="left:737px;top:883px;width:18px;height:18px" href="#"><svg viewBox="0 0 6 6"><path d="M2 0.5 4.5 3 2 5.5" fill="none" stroke="#fff" stroke-width="1.2"/></svg></a>
<article class="abs card" style="left:114px"><div class="pic" role="img" aria-label="Portrait of a female doctor with stethoscope"></div><h5>Dr. Nora Pellham</h5><span>Pediatric Clinic</span></article>
<article class="abs card" style="left:272px"><div class="pic" role="img" aria-label="Portrait of a male doctor in white coat and red tie"></div><h5>Dr. Owen Talbrook</h5><span>Cardiac Clinic</span></article>
<article class="abs card" style="left:430px"><div class="pic" role="img" aria-label="Portrait of a female nurse in green scrubs"></div><h5>Dr. Lena Marsk</h5><span>Rehabilitation Therapy</span></article>
<article class="abs card" style="left:589px"><div class="pic" role="img" aria-label="Portrait of a male doctor with stethoscope"></div><h5>Dr. Rafe Coldwell</h5><span>Laryngological Clinic</span></article>
<a class="abs btn-lg" style="left:338px;width:64px;background:var(--blue)" href="#">View All</a>
<a class="abs btn-lg" style="left:407px;width:100px;background:var(--blue-dark)" href="#">Staff Schedule</a>

<div class="abs footer-line"></div>
<footer class="abs footer">
  <div class="abs brand"><span class="dot"></span><span class="name">Cedarview Clinics</span></div>
  <p class="about-f">Lorem Ipsum is simply dummy text of the printing and typesetting industry. Lorem Ipsum has been the industry's standard dummy text ever since</p>
  <div class="col" style="left:325px">
    <h6>Navigation</h6>
    <div class="current">Home</div><div>Our Clinic</div><div>Newsletter</div><div>Our Staff</div><div>Resources</div>
  </div>
  <div class="col" style="left:483px">
    <h6>Links</h6>
    <div>Help</div><div>Support</div><div>Privacy Policy</div>
  </div>
  <div class="col" style="left:589px">
    <h6>Contact Us</h6>
    <table>
      <tr><td>Telephone :</td><td>604-318-4402</td></tr>
      <tr><td>Email:</td><td>hello@cedarviewclinics.ca</td></tr>
      <tr><td>Address:</td><td>48 Alder Row<br>Harbourton, Canada,<br>K2M 7QP</td></tr>
    </table>
  </div>
</footer>
<div class="abs base">
  <span class="abs copy">© 2015 Cedarview Clinics. All Rights Reservsd</span>
  <nav class="abs links"><a href="#">About Us</a><a href="#">Terms of Use</a><a href="#">Privacy Policy</a></nav>
</div>

</body>
</html>
```